FinTech company looking to revamp and expand client-facing interface for our financial models

Pellworth Engines currently has a very simple website that allows clients to interact with our financial models. We are looking to completely redesign the current site and add several extra pages to provide extra functionality. We want the design to have a modern, slick feel, that will work on both a desktop or a tablet. It should be straightforward for clients to move between different pages at any time, and clear from the layout how to interact with the more advanced features. We have included screenshots of existing pages in the attached design brief, as well as sketches of the functionality required by the new pages, but can't provide a direct link to the current site.
Target Market(s)
Professional investors that will be paying to access the interface
Industry/Entity Type
Finance
Number of Pages Required
4 page
Colors
Designer to choose colors to be used in the design.
Look and feel
Each slider illustrates characteristics of the customer's brand and the style your logo design should communicate.

```html
<!DOCTYPE html>
<html lang="en">
<head>
<meta charset="utf-8">
<title>Korvex – Models</title>
<link rel="stylesheet" href="https://fonts.googleapis.com/css2?family=Roboto:wght@400;500;700&family=Roboto+Condensed:wght@400;500&display=swap">
<style>
  :root {
    --page-bg: #e6e6e6;
    --panel-bg: #ffffff;
    --bar-top: #fafafa;
    --bar-bottom: #c9c9c9;
    --tab-active: #444444;
    --tab-active-text: #ffffff;
    --text: #111111;
    --divider: #0b0b4f;
    --subtab-top: #f4f4f4;
    --subtab-bottom: #c8c8c8;
    --subtab-text: #555555;
    --input-border: #cfcfcf;
    --link: #1a3d8a;
    --table-head: #8a8a8a;
    --row-top: #ffffff;
    --row-bottom: #dedede;
    --cell-line: #cfcfcf;
  }
  * { box-sizing: border-box; margin: 0; padding: 0; }
  html, body { width: 1200px; height: 757px; overflow: hidden; background: var(--page-bg); }
  body { font-family: "Roboto", Arial, sans-serif; color: var(--text); }

  .stage { width: 1300px; height: 820px; transform: scale(0.923077); transform-origin: 0 0; position: relative; background: var(--page-bg); }
  .panel { position: absolute; left: 15px; top: 15px; width: 1270px; height: 790px; background: var(--panel-bg); }

  .topbar { position: absolute; left: 0; top: 0; width: 1270px; height: 60px; display: flex;
    background: linear-gradient(var(--bar-top), var(--bar-bottom)); }
  .brand { width: 180px; padding-left: 58px; line-height: 60px; font-weight: 700; font-size: 18px; }
  .period { width: 90px; text-align: center; line-height: 60px; font-weight: 700; font-size: 14px; border-right: 1px solid #d6d6d6; }
  .period.is-active { background: var(--tab-active); color: var(--tab-active-text); border-right: 0; }
  .topbar .spacer { flex: 1; }
  .main-nav { display: flex; align-items: center; justify-content: center; gap: 8px; font-weight: 700; font-size: 13px; border-left: 1px solid #d6d6d6; }
  .main-nav.is-active { background: #1b1b1b; color: #fff; border-left: 0; }
  .main-nav svg { width: 22px; height: 22px; }

  .divider { position: absolute; left: 0; top: 109px; width: 1270px; height: 3px; background: var(--divider); }
  .subbar { position: absolute; left: 0; top: 112px; width: 1270px; height: 68px;
    background: linear-gradient(#ffffff, #dcdcdc); }
  .subtabs { position: absolute; left: 237px; top: 14px; display: flex; gap: 5px; }
  .subtab { width: 155px; height: 54px; border-radius: 6px 6px 0 0; text-align: center;
    background: linear-gradient(var(--subtab-top), var(--subtab-bottom)); color: var(--subtab-text);
    font-size: 13px; font-weight: 500; padding-top: 8px; }
  .subtab svg { display: block; margin: 0 auto 6px; width: 20px; height: 18px; }

  .filters { position: absolute; left: 57px; top: 220px; font-size: 16px; }
  .filter-row { display: flex; align-items: center; height: 30px; margin-bottom: 10px; }
  .filter-row .label { width: 187px; }
  .filter-row b { font-weight: 700; }
  .filter-row input { width: 181px; height: 30px; border: 2px solid var(--input-border); border-radius: 4px;
    padding: 0 12px; font: 16px "Roboto", Arial, sans-serif; color: var(--text); }

  .export { position: absolute; left: 1125px; top: 262px; display: flex; align-items: center; gap: 8px;
    color: var(--link); font-weight: 700; font-size: 17px; }
  .export svg { width: 26px; height: 24px; }

  .models { position: absolute; left: 55px; top: 320px; width: 1160px; border-collapse: collapse;
    border-radius: 8px; overflow: hidden; box-shadow: 0 4px 12px rgba(0,0,0,0.15); table-layout: fixed; }
  .models th { background: var(--table-head); color: #fff; font-weight: 500; font-size: 17px; height: 70px;
    border-right: 1px solid #a0a0a0; }
  .models th:last-child, .models td:last-child { border-right: 0; }
  .models td { height: 69px; font-family: "Roboto Condensed", "Arial Narrow", sans-serif; font-size: 17px;
    background: linear-gradient(var(--row-top), var(--row-bottom)); border-right: 1px solid var(--cell-line);
    padding-left: 9px; line-height: 1.25; }
  .models td.id, .models td.time, .models td.quality { text-align: center; padding-left: 0; }
</style>
</head>
<body>
<div class="stage">
  <div class="panel">
    <header class="topbar">
      <div class="brand">KORVEX</div>
      <div class="period is-active">250D</div>
      <div class="period">83D</div>
      <div class="period">42D</div>
      <div class="spacer"></div>
      <div class="main-nav is-active" style="width:141px">
        <svg viewBox="0 0 24 24" fill="none" stroke="#fff" stroke-width="2"><path d="M3 11 12 3l9 8M5 10v11h5v-6h4v6h5V10"/></svg>MODELS
      </div>
      <div class="main-nav" style="width:178px">
        <svg viewBox="0 0 24 24" fill="none" stroke="#222" stroke-width="1.4"><circle cx="12" cy="12" r="3"/><circle cx="12" cy="12" r="7" stroke-dasharray="2 2"/><circle cx="12" cy="12" r="10" stroke-dasharray="1.5 2.5"/></svg>SENSITIVITIES
      </div>
      <div class="main-nav" style="width:197px">
        <svg viewBox="0 0 24 24" fill="none" stroke="#222" stroke-width="1.8"><path d="m12 2 3 7 7 .6-5.3 4.7 1.6 7.2L12 17.8 5.7 21.5l1.6-7.2L2 9.6 9 9z"/></svg>FAVOURITES
      </div>
    </header>

    <div class="divider"></div>
    <nav class="subbar">
      <div class="subtabs">
        <div class="subtab"><svg viewBox="0 0 20 18" fill="#555"><rect x="0" y="2" width="20" height="2"/><rect x="0" y="8" width="14" height="2"/><rect x="16" y="8" width="4" height="2"/><rect x="0" y="14" width="20" height="2"/></svg>EQUITIES</div>
        <div class="subtab"><svg viewBox="0 0 20 18" fill="#555"><rect x="1" y="11" width="3" height="7"/><rect x="6" y="8" width="3" height="10"/><rect x="11" y="10" width="3" height="8"/><rect x="16" y="5" width="3" height="13"/><path d="M1 8 7 3l5 3 6-5" stroke="#555" stroke-width="1.5" fill="none"/></svg>ETFS</div>
        <div class="subtab"><svg viewBox="0 0 20 18" fill="none" stroke="#555" stroke-width="1.8"><circle cx="9" cy="10" r="7"/><circle cx="9" cy="10" r="3"/><path d="M9 10 17 2"/></svg>PAIRS</div>
        <div class="subtab"><svg viewBox="0 0 20 18" fill="none" stroke="#555" stroke-width="1.6"><rect x="3" y="1" width="14" height="16" rx="1"/><path d="M6 5h8M6 9h8M6 13h8"/></svg>ETF PAIRS</div>
        <div class="subtab"><svg viewBox="0 0 20 18" fill="#555"><path d="M7 3 13 1v16l-6-2z"/></svg>FACTORS</div>
      </div>
    </nav>

    <form class="filters">
      <div class="filter-row"><span class="label">Quality &nbsp;&nbsp;&nbsp;&nbsp;<b>Threshold:</b></span><input type="text" value="-10"></div>
      <div class="filter-row"><span class="label"><b>Abs.</b> Stat &nbsp;<b>Threshold:</b></span><input type="text" value="-10"></div>
    </form>

    <div class="export">
      <svg viewBox="0 0 26 24" fill="none" stroke="#1a3d8a" stroke-width="2.2"><path d="M11 5H5a2 2 0 0 0-2 2v12a2 2 0 0 0 2 2h13a2 2 0 0 0 2-2v-5"/><path d="M10 15c1-5 5-8 12-8M18 3l4 4-4 4"/></svg>Export
    </div>

    <table class="models">
      <colgroup>
        <col style="width:100px"><col style="width:110px"><col style="width:115px"><col style="width:115px">
        <col style="width:90px"><col style="width:90px"><col style="width:90px"><col style="width:90px">
        <col style="width:90px"><col style="width:90px"><col style="width:90px"><col style="width:90px">
      </colgroup>
      <thead>
        <tr><th>ID &#8964;</th><th>Sector</th><th>Time</th><th>Quality</th><th>Stat 1</th><th>Stat 2</th><th>Stat 3</th><th>Stat 4</th><th>Stat 5</th><th>Stat 6</th><th>Stat 7</th><th>Stat 8</th></tr>
      </thead>
      <tbody>
        <tr><td class="id">Model 1</td><td>Materials</td><td class="time">2019-07-03<br>12:15:00.000</td><td class="quality">30.2288</td><td>2.01574</td><td>23.305</td><td>-0.149368</td><td>22.3054</td><td>4.63714</td><td>0.945706</td><td>2.81949</td><td>2.60858</td></tr>
        <tr><td class="id">Model 2</td><td>Industrials</td><td class="time">2019-07-03<br>12:15:00.000</td><td class="quality">32.8694</td><td>0.87307</td><td>32.185</td><td>-0.033692</td><td>33.9911</td><td>11.5693</td><td>-0.472968</td><td>-0.830458</td><td>6.80646</td></tr>
        <tr><td class="id">Model 3</td><td>Consumer<br>Discretionary</td><td class="time">2019-07-03<br>12:15:00.000</td><td class="quality">1.66002</td><td>-0.569222</td><td>159.814</td><td>0.0252328</td><td>172.616</td><td>10.2875</td><td>-0.750396</td><td>-0.385309</td><td>4.69146</td></tr>
        <tr><td class="id">Model 4</td><td>Information<br>Technology</td><td class="time">2019-07-03<br>12:15:00.000</td><td class="quality">45.6856</td><td>0.412148</td><td>202.488</td><td>0.0084923</td><td>205.834</td><td>11.9094</td><td>-0.137913</td><td>0.449595</td><td>3.85106</td></tr>
        <tr><td class="id">Model 5</td><td>Information<br>Technology</td><td class="time">2019-07-03<br>12:15:00.000</td><td class="quality">75.7733</td><td>7.06728</td><td>188.605</td><td>0.016913</td><td>161.665</td><td>3.82241</td><td>0.981019</td><td>1.29847</td><td>3.34927</td></tr>
      </tbody>
    </table>
  </div>
</div>
</body>
</html>
```